We need a redesign of our current website: www.halvenridgegroup.com. Halvenridge Group is a fully integrated hospitality development, management, and investment firm. We strive for leadership in each of our segments by building quality assets, exacting high standards of customer service, and focusing on returns for our investors and partners.

It is our mission to provide our guests an exceptional lodging experience; our clients an unsurpassed level of management in their properties; and create positive returns for our investors and partners. We achieve our mission via a company culture of transparency, ownership of our actions, and accountability for our results.

Target Market(s)

hotel owners, hotel developers, hotel investors, bankers

Industry/Entity Type

Hospitality

Requirements
Must have
• Our logo has to be there along with the quote and the ability to convey the following quote off of our current website: "Halvenridge was founded on the principles of integrity, honesty, loyalty, and trust. These convictions embody our company at every level, and show in every action."

```html
<!DOCTYPE html>
<html lang="en">
<head>
<meta charset="utf-8">
<title>Halvenridge Group</title>
<link href="https://fonts.googleapis.com/css2?family=Source+Sans+3:ital,wght@0,400;0,600;0,700;1,400;1,600&display=swap" rel="stylesheet">
<style>
:root{
  --gold:#d88a06;
  --gold-dark:#b96f00;
  --gold-text:#c98a12;
  --ink:#3a3a3a;
  --muted:#777;
  --page:#f7f7f7;
  --black:#0b0b0b;
  --footer:#1d1d1d;
  --white:#fff;
}
*{box-sizing:border-box;margin:0;padding:0}
html,body{width:883px;height:1200px;overflow:hidden}
body{position:relative;background:var(--page);font-family:"Source Sans 3",Arial,sans-serif;color:var(--ink)}
.abs{position:absolute}
/* header */
.site-header{left:0;top:0;width:883px;height:97px;background:linear-gradient(#f4f4f4,#e9e9e9);border-bottom:2px solid var(--gold)}
.brand{left:96px;top:27px;display:flex;align-items:center;gap:10px}
.brand-mark{width:52px;height:52px;border-radius:50%;background:var(--gold)}
.brand-name{font-size:22px;font-weight:600;letter-spacing:2.5px;color:var(--gold);line-height:22px}
.main-nav{left:439px;top:40px;display:flex;align-items:center}
.main-nav a{font-size:12.5px;color:var(--gold);text-decoration:none;padding:0 11px;height:23px;line-height:23px;border-left:1px solid #bbb}
.main-nav a.current{background:#2a2625;color:var(--white);border-radius:3px;border:none;width:61px;text-align:center;padding:0;margin-right:7px}
.main-nav a.current+a{border-left:none}
/* hero */
.hero-band{left:0;top:99px;width:883px;height:376px;background:var(--black)}
.hero-frame{left:96px;top:130px;width:691px;height:313px;background:var(--white);padding:4px}
.hero-photo{width:100%;height:100%;background:linear-gradient(180deg,#cfd2d6 0%,#e8c460 45%,#d9a646 70%,#8b7a5a 100%)}
.hero-caption{left:100px;top:313px;width:260px;height:125px;background:rgba(216,138,6,.92);padding:8px 26px;color:var(--white);font-weight:600;line-height:1.15}
.hero-caption .small{font-size:18px}
.hero-caption .big{font-size:25px}
.slider-dots{left:126px;top:409px;display:flex;gap:4px;align-items:center}
.slider-dots span{width:8px;height:8px;border-radius:50%;background:var(--white)}
.slider-dots span.arrow{width:11px;height:11px;background:#111}
.slider-dots span.active{background:#333}
/* quote */
.quote{left:155px;top:458px;width:573px;height:67px;background:linear-gradient(#fff,#eaeaea);border:1px solid #ccc;border-radius:0 0 14px 14px;text-align:center;padding-top:9px;box-shadow:0 6px 8px -6px rgba(0,0,0,.25)}
.quote p{font-style:italic;font-size:11.5px;color:#444;line-height:16px;padding:0 30px}
.quote cite{display:block;margin-top:3px;font-size:10px;font-style:normal;color:#555}
.quote cite b{font-style:italic;font-weight:600;font-size:11.5px;color:var(--gold-text);margin-right:4px}
/* services */
.content{left:88px;top:475px;width:707px;height:565px;background:#f9f9f9}
.service{top:550px;width:215px}
.service h2{display:flex;align-items:flex-end;gap:8px;font-size:19px;font-weight:400;letter-spacing:.5px;color:#555;height:32px}
.service h2 .dot{width:22px;height:22px;border-radius:50%;background:var(--gold);margin-bottom:3px}
.service h2 .cap{font-size:32px;color:var(--gold);line-height:30px;margin-right:-8px}
.service p{margin-top:14px;font-size:10.5px;line-height:15px;color:#777}
.btn{display:inline-block;width:63px;height:22px;border-radius:3px;background:linear-gradient(#e19a1e,var(--gold-dark));color:var(--white);font-size:12px;text-align:center;line-height:22px;text-decoration:none}
.service .btn{position:absolute;top:125px;left:0}
/* panel */
.panel{left:96px;top:727px;width:691px;height:330px;background:linear-gradient(#f1f1f1,#e9e9e9);border:1px solid #ddd;border-radius:8px}
.section-title{font-size:18px;font-weight:400;color:#444;letter-spacing:.3px}
.about-text{left:111px;top:777px;width:441px;font-size:11px;letter-spacing:.35px;line-height:17px;color:#666;text-align:justify}
.view-all{left:508px;top:893px;font-size:12px;font-weight:600;color:#333;text-decoration:underline}
.project{top:924px;width:138px}
.project .thumb{height:76px;background:#fff;border:1px solid #d8d8d8;padding:4px}
.project .thumb div{width:100%;height:100%}
.project p{margin-top:5px;font-size:10px;line-height:12px;font-style:italic;font-weight:600;color:var(--gold-text)}
.team-arrows{left:729px;top:748px;display:flex;gap:2px}
.team-arrows span{width:21px;height:18px;border-radius:3px;display:flex;align-items:center;justify-content:center}
.member{left:577px;width:200px}
.member .portrait{width:64px;height:64px;background:#fff;border:1px solid #d6d6d6;padding:3px}
.member .portrait div{width:100%;height:100%;background:linear-gradient(#8a8a8a,#4a4a4a)}
.member .info{position:absolute;left:74px;top:0;width:126px}
.member .role{font-size:10px;color:#333}
.member .name{font-size:13px;font-weight:600;color:var(--gold-text);margin-top:2px}
.member .bio{font-size:10px;line-height:13px;color:#777;margin-top:6px}
.member .read{display:block;font-size:10px;color:#8a6a20;text-decoration:underline;margin-top:9px}
/* footer */
.site-footer{left:0;top:1040px;width:883px;height:160px;background:var(--footer)}
.foot-col h3{font-size:13px;font-weight:600;color:var(--white);margin-bottom:2px}
.foot-col li{list-style:none;font-size:9px;color:#ddd;line-height:17.5px;text-transform:uppercase}
.connect li{display:flex;align-items:center;gap:9px;line-height:18px}
.connect i{width:11px;height:11px;border-radius:50%;background:#4a7ab0;display:inline-block}
.newsletter{left:333px;top:1062px;width:220px;height:120px;background:#0d0d0d;border-radius:3px;padding:8px 11px}
.newsletter h3{font-size:13px;font-weight:600;color:var(--white);margin-bottom:9px}
.newsletter .field{width:184px;height:20px;background:var(--white);font-size:10px;line-height:20px;padding-left:7px;color:#333;margin-bottom:6px}
.newsletter .subscribe{position:absolute;right:24px;top:88px;width:79px;height:24px;background:linear-gradient(#e7a127,var(--gold-dark));border-radius:3px;color:var(--white);font-size:12px;font-weight:600;text-align:center;line-height:24px}
.contact{left:613px;top:1062px;color:#ddd;font-size:9.5px;line-height:19px;font-style:normal}
.contact h3{font-size:13px;font-weight:600;color:var(--white);margin-bottom:0}
.contact strong{color:var(--white);font-size:11px}
.contact .gold{color:var(--gold);font-size:11px}
.contact .mail{color:var(--gold);font-size:9.5px}
</style>
</head>
<body>
<header class="site-header abs">
  <div class="brand abs"><span class="brand-mark"></span><span class="brand-name">HALVENRIDGE<br>GROUP</span></div>
  <nav class="main-nav abs">
    <a class="current" href="#">HOME</a><a href="#">SERVICES</a><a href="#">PROJECTS</a><a href="#">TEAM</a><a href="#">CONTACT US</a>
  </nav>
</header>

<section class="hero-band abs"></section>
<div class="hero-frame abs"><div class="hero-photo" role="img" aria-label="Photo of a yellow three-storey hotel with a covered entrance under a cloudy sky"></div></div>
<div class="hero-caption abs">
  <div class="small">We Strive for</div>
  <div><span class="big">Leadership</span> <span class="small">in each</span></div>
  <div><span class="small">of our</span> <span class="big">Segments.</span></div>
</div>
<div class="slider-dots abs"><span class="arrow"></span><span class="active"></span><span></span><span></span><span></span><span class="arrow"></span></div>

<div class="content abs"></div>

<blockquote class="quote abs">
  <p>"Halvenridge was founded on the principles of integrity, honesty, loyalty, and trust. These convictions embody our company at every level, and show in every action."</p>
  <cite><b>Ravi Dessai</b>( President and CEO )</cite>
</blockquote>

<section class="service abs" style="left:104px">
  <h2><span class="dot"></span><span class="cap">D</span>EVELOPMENT</h2>
  <p>When evaluating sites for purchase and hotel development, our experienced team conducts the full array of feasibility studies and market analyses......</p>
  <a class="btn" href="#">More</a>
</section>
<section class="service abs" style="left:339px;width:205px">
  <h2><span class="dot"></span><span class="cap">M</span>ANAGEMENT</h2>
  <p>Using proven strategies we maximize potential &nbsp;and produce profitable results for your &nbsp;hotel, &nbsp;just as we do with our own......</p>
  <a class="btn" href="#">More</a>
</section>
<section class="service abs" style="left:574px">
  <h2><span class="dot"></span><span class="cap">I</span>NVESTMENT</h2>
  <p>Halvenridge recognizes &nbsp;that we are entrusted with investors' capital. In honoring this trust we aim to create and realize shareholder value through the acquisition......</p>
  <a class="btn" href="#">More</a>
</section>

<div class="panel abs"></div>
<h2 class="section-title abs" style="left:111px;top:746px">ABOUT HALVENRIDGE GROUP</h2>
<p class="about-text abs">Halvenridge Group is a fully integrated hospitality development, management, and investment firm. We strive for leadership in each of our segments by building quality assets, exacting high standards of customer service, and focusing on returns for our investors and partners.</p>
<a class="btn abs" href="#" style="left:110px;top:855px">More</a>

<h2 class="section-title abs" style="left:111px;top:889px">OUR PROJECTS</h2>
<a class="view-all abs" href="#">View All</a>
<div class="project abs" style="left:110px">
  <div class="thumb"><div role="img" aria-label="Photo of a brick inn with a parking lot" style="background:linear-gradient(#c9d6e6,#a7877a 55%,#7c7a78)"></div></div>
  <p>Meadowbrook Inn &amp; Suites<br>Cincinnati, OH</p>
</div>
<div class="project abs" style="left:261px">
  <div class="thumb"><div role="img" aria-label="Photo of a roadside hotel with a blue sign" style="background:linear-gradient(#d9dfe6,#b8b8b0 50%,#3b5a8a)"></div></div>
  <p>Roadside Lodge<br>Florence, KY</p>
</div>
<div class="project abs" style="left:413px">
  <div class="thumb"><div role="img" aria-label="Photo of a modern hotel under a blue sky" style="background:linear-gradient(#2e63b8,#7fa4d4 45%,#e7e3d6 75%,#7b8b6a)"></div></div>
  <p>Harborgate Hotel<br>Blue Ash, OH</p>
</div>

<h2 class="section-title abs" style="left:577px;top:746px">OUR TEAM</h2>
<div class="team-arrows abs">
  <span style="background:var(--gold)"><svg width="6" height="8" viewBox="0 0 6 8"><path d="M5 0 1 4l4 4" fill="none" stroke="#fff" stroke-width="1.5"/></svg></span>
  <span style="background:#555"><svg width="6" height="8" viewBox="0 0 6 8"><path d="M1 0l4 4-4 4" fill="none" stroke="#fff" stroke-width="1.5"/></svg></span>
</div>
<article class="member abs" style="top:780px">
  <div class="portrait"><div role="img" aria-label="Portrait of the President and CEO"></div></div>
  <div class="info">
    <div class="role">President &amp; CEO</div>
    <div class="name">Ravi Dessai</div>
    <p class="bio">As the President and CEO of Halvenridge, Ravi provides the vision and strategic direction for the company.</p>
    <a class="read" href="#">Read More</a>
  </div>
</article>
<article class="member abs" style="top:914px">
  <div class="portrait"><div role="img" aria-label="Portrait of the Vice President Operations"></div></div>
  <div class="info">
    <div class="role">Vice President Operations</div>
    <div class="name">Colin Marsh</div>
    <p class="bio">Colin is a talented management professional with more than 15 years of hands-on, day-to-day ....</p>
    <a class="read" href="#">Read More</a>
  </div>
</article>

<footer class="site-footer abs"></footer>
<div class="foot-col abs" style="left:96px;top:1062px">
  <h3>COMPANY</h3>
  <ul><li>Home</li><li>Services</li><li>Projects</li><li>Team</li><li>Contact</li></ul>
</div>
<div class="foot-col connect abs" style="left:213px;top:1062px">
  <h3>CONNECT</h3>
  <ul>
    <li><i></i>Circlebook</li>
    <li><i style="background:#3aa6d8"></i>Chirpline</li>
    <li><i style="background:#3c77a8"></i>Linkwork</li>
    <li><i style="background:#e0761c"></i>RSS</li>
  </ul>
</div>
<div class="newsletter abs">
  <h3>Newsletter SignUp</h3>
  <div class="field">Name</div>
  <div class="field">Email Address</div>
  <div class="subscribe">Subscribe</div>
</div>
<address class="contact abs">
  <h3>Contact Us</h3>
  <div>4180 Lindenwood Ave.</div>
  <div>#210, Brookhaven, OH 45290</div>
  <div><strong>Ph:</strong> <span class="gold">555.013.2870</span></div>
  <div><strong>Email :</strong> <span class="mail">info@halvenridgegroup.com</span></div>
</address>
</body>
</html>
```